Business Card Design

I give lessons and clinics for dressage riders
I would like the design to be an outline (with broad lines) of a dressage horse and rider with in background of whole card with print over top tan or parchment card with burgundy print

Industry/Entity Type

Business

Contact Information for Business Card

Dale Ferrin
612-374-2059
Classical dressage training for the modern American
Clinics, lessons, training level -Prix St. George

Requirements
Must have
• broad lined outline of dressage horse and rider

```html
<!DOCTYPE html>
<html lang="en">
<head>
<meta charset="utf-8">
<title>Dale Ferrin — Classical Dressage Business Card</title>
<link rel="stylesheet" href="https://fonts.googleapis.com/css2?family=Almendra+SC&display=swap">
<style>
  :root {
    --parchment: #ecd9bb;
    --parchment-light: #f1e2c8;
    --parchment-edge: #b98c86;
    --burgundy: #5a1627;
    --burgundy-soft: #7a3340;
    --card-w: 1200px;
    --card-h: 693px;
  }
  * { box-sizing: border-box; margin: 0; padding: 0; }
  html, body {
    width: var(--card-w);
    height: var(--card-h);
    overflow: hidden;
    background: var(--parchment);
  }
  .business-card {
    position: relative;
    width: var(--card-w);
    height: var(--card-h);
    overflow: hidden;
    background:
      radial-gradient(ellipse 75% 70% at 50% 48%, var(--parchment-light) 0%, var(--parchment) 55%, #dcbfa3 82%, var(--parchment-edge) 100%);
    color: var(--burgundy);
    font-family: "Almendra SC", "Georgia", serif;
  }
  .rider-illustration {
    position: absolute;
    left: 514px;
    top: 17px;
    width: 228px;
    height: 452px;
    border-radius: 40px 40px 30px 30px;
    background: linear-gradient(180deg, var(--burgundy-soft) 0%, var(--burgundy) 100%);
    opacity: 0.85;
  }
  .contact-row {
    position: absolute;
    left: 85px;
    right: 82px;
    top: 462px;
    display: flex;
    justify-content: space-between;
    align-items: baseline;
    font-size: 58px;
    line-height: 1;
    letter-spacing: 1px;
  }
  .divider {
    position: absolute;
    left: 85px;
    top: 540px;
    width: 1033px;
    height: 8px;
  }
  .services {
    position: absolute;
    left: 0;
    right: 0;
    top: 578px;
    text-align: center;
    font-size: 29px;
    line-height: 43px;
    letter-spacing: 0.5px;
    text-transform: uppercase;
  }
</style>
</head>
<body>
  <main class="business-card">
    <div class="rider-illustration" role="img" aria-label="Broad-lined burgundy outline of a dressage horse and rider in top hat, shown head-on at a collected trot"></div>

    <div class="contact-row">
      <span class="trainer-name">DALE FERRIN</span>
      <span class="trainer-phone">612-374-2059</span>
    </div>

    <svg class="divider" viewBox="0 0 1033 8" preserveAspectRatio="none" aria-hidden="true">
      <path d="M0 4 Q 6 0.5 20 1.5 L 1010 1.8 Q 1030 2 1033 4 Q 1030 6.5 1010 6.3 L 20 6.5 Q 6 7.5 0 4 Z" fill="var(--burgundy)"/>
    </svg>

    <div class="services">
      <p class="tagline">Classical dressage training for the modern American</p>
      <p class="offerings">Clinics, lessons, training level -Prix St. George</p>
    </div>
  </main>
</body>
</html>
```